Business Card Design Project

Looking to update our business cards. We have a logo with our slogan. We are an IT firm so we wouldlike a modern look.

Industry/Entity Type

Business

```html
<!DOCTYPE html>
<html lang="en">
<head>
<meta charset="utf-8">
<title>Vantix Business Card — Front and Back</title>
<link rel="stylesheet" href="https://fonts.googleapis.com/css2?family=Cinzel:wght@400;700;900&family=Open+Sans:wght@400&display=swap">
<style>
  :root {
    --board-light: #ececec;
    --board-mid: #d3d3d3;
    --board-dark: #a9a9a9;
    --card-black: #000000;
    --brand-green: #5fa829;
    --ink-white: #ffffff;
    --label-ink: #0a0a0a;
    --art-navy: #0b1a2e;
    --art-teal: #123f3c;
  }
  * { margin: 0; padding: 0; box-sizing: border-box; }
  html, body { width: 1184px; height: 1200px; overflow: hidden; }
  body {
    position: relative;
    background: radial-gradient(ellipse 70% 60% at 50% 48%, var(--board-light) 0%, var(--board-mid) 55%, var(--board-dark) 100%);
    font-family: "Cinzel", serif;
  }

  .side-label {
    position: absolute;
    font-family: "Cinzel", serif;
    font-weight: 900;
    font-size: 60px;
    line-height: 1;
    color: var(--label-ink);
    letter-spacing: 1px;
  }
  .side-label--front { left: 905px; top: 242px; }
  .side-label--back { left: 92px; top: 812px; }

  .card {
    position: absolute;
    background: var(--card-black);
    overflow: hidden;
  }
  .card--front { left: 66px; top: 71px; width: 795px; height: 502px; }
  .card--back { left: 349px; top: 606px; width: 798px; height: 493px; }

  .brand-name {
    position: absolute;
    left: 0; right: 0; top: 70px;
    text-align: center;
    font-family: "Cinzel", serif;
    font-weight: 700;
    font-size: 58px;
    letter-spacing: 10px;
    color: var(--brand-green);
  }

  .hero-artwork {
    position: absolute;
    left: 28px; top: 215px; width: 740px; height: 270px;
    background: linear-gradient(135deg, var(--art-navy) 0%, var(--art-teal) 100%);
  }

  .bracket {
    position: absolute;
    width: 54px; height: 66px;
    border-color: var(--brand-green);
    border-style: solid;
  }
  .bracket--top-left { left: 26px; top: 22px; border-width: 4px 0 0 4px; }
  .bracket--bottom-right { left: 713px; top: 397px; width: 54px; height: 68px; border-width: 0 4px 4px 0; }

  .holder-name {
    position: absolute;
    left: 0; right: 0; top: 154px;
    text-align: center;
    font-weight: 700;
    font-size: 46px;
    color: var(--ink-white);
    letter-spacing: 1px;
  }
  .holder-position {
    position: absolute;
    left: 0; right: 0; top: 214px;
    text-align: center;
    font-weight: 700;
    font-size: 31px;
    color: var(--ink-white);
    letter-spacing: 1px;
  }

  .contact-block {
    position: absolute;
    color: var(--ink-white);
    font-size: 19px;
    line-height: 29px;
  }
  .contact-block--left { left: 38px; top: 402px; }
  .contact-block--right { left: 511px; top: 410px; line-height: 31px; }
  .contact-key { font-family: "Cinzel", serif; font-weight: 700; font-size: 20px; }
  .contact-value { font-family: "Open Sans", sans-serif; font-size: 18px; }
</style>
</head>
<body>
  <div class="side-label side-label--front">Front</div>
  <div class="side-label side-label--back">Back</div>

  <section class="card card--front">
    <div class="brand-name">VANTIX</div>
    <div class="hero-artwork" role="img" aria-label="Abstract technology artwork of green light streaks and circuit lines on a dark blue background"></div>
  </section>

  <section class="card card--back">
    <div class="bracket bracket--top-left"></div>
    <div class="bracket bracket--bottom-right"></div>
    <div class="holder-name">YOUR NAME HERE</div>
    <div class="holder-position">YOUR POSITION</div>
    <div class="contact-block contact-block--left">
      <div><span class="contact-key">Email :</span> <span class="contact-value">yourname@xxx.com</span></div>
      <div><span class="contact-key">Web</span> <span class="contact-value">: www.websitename.com</span></div>
    </div>
    <div class="contact-block contact-block--right">
      <div><span class="contact-key">Phone :</span> <span class="contact-value">00-11-222-3333</span></div>
      <div><span class="contact-key">Fax:</span> <span class="contact-value">00-11-222-3333</span></div>
    </div>
  </section>
</body>
</html>
```